Desktop and Networking Support Course 9.17.25

Important the ad should not be very busy with the text taking up the major part of the ad .. please do not make the text so big that it takes up most of the ad..
Flyer Design Brief for Graphic Artist
also i am looking for something unique or creative that it will stand out .
Size & Layout:
Full Page with Bleed: 8” x 10.75” + 0.25” bleed on all sides.
Footer Space: Leave a 1-inch margin at the bottom for footer content (e.g., contact info, logo, or call-to-action).
Target Audience:
College-age students (around 24 years old)
Located in the USA
Interested in creative, professional, and career-building opportunities
Purpose:
To attract students to enroll in a college program
Flyer should be eye-catching, unique, and creative
Text must be clear and readable,
Design Style:
Use vector art, typography, or photography — your choice
If using photography, feature a white young professional USA citizen:
Wearing a white collared shirt
not with long hair
Creative Direction:
The flyer should stand out visually — something people would want to look at and keep
Showcase creativity and professionalism
Use bold colors, dynamic layout, or unexpected design elements to grab attention
Avoid clutter — keep the design balanced and clean
Text Suggestions (can be adjusted):
Footer,
please leave one inch on the bottom for the footer

```html
<!DOCTYPE html>
<html lang="en">
<head>
<meta charset="utf-8">
<title>Desktop &amp; Network Support Course Flyer</title>
<link href="https://fonts.googleapis.com/css2?family=Oswald:wght@500;600;700&family=Montserrat:wght@500;600;700&display=swap" rel="stylesheet">
<style>
  :root {
    --green: #2fb84e;
    --ink: #1f1f21;
    --navy: #161a28;
    --paper: #f4f4f3;
    --grey-band: #777778;
    --grey-text: #4a4a4c;
    --page-bg: #e9ebe9;
  }
  * { margin: 0; padding: 0; box-sizing: border-box; }
  html, body {
    width: 1200px; height: 900px; overflow: hidden;
    background: var(--page-bg);
  }
  .flyer {
    position: absolute; left: 297px; top: 20px;
    width: 803px; height: 1139px;
    transform: scale(0.755); transform-origin: top left;
    background: var(--paper);
    box-shadow: 0 10px 40px rgba(0,0,0,0.18);
    overflow: hidden;
  }
  .flyer-shapes { position: absolute; inset: 0; }
  .display { font-family: "Oswald", "Arial Narrow", sans-serif; font-weight: 700; text-transform: uppercase; line-height: 1; white-space: nowrap; }
  .sans { font-family: "Montserrat", "Helvetica", sans-serif; line-height: 1; white-space: nowrap; }
  .title-line { position: absolute; left: 34px; display: block; }
  .title-desktop { top: 107px; color: var(--green); font-size: 90px; letter-spacing: -1px; }
  .title-network { top: 196px; color: var(--ink); font-size: 68px; letter-spacing: -1px; }
  .title-course { top: 261px; color: var(--green); font-size: 48px; letter-spacing: -1.5px; }
  .subtitle { position: absolute; left: 35px; top: 318px; font-size: 15px; font-weight: 600; color: var(--grey-text); letter-spacing: 0.2px; }
  .employment { position: absolute; left: 39px; top: 377px; color: #fff; font-size: 34px; font-weight: 600; letter-spacing: 0.2px; }
  .class-year { position: absolute; left: 38px; top: 434px; color: var(--green); font-size: 33px; font-weight: 700; letter-spacing: 0.3px; }
  .headline { position: absolute; left: 406px; top: 579px; color: #fff; font-size: 60px; line-height: 75px; font-weight: 700; letter-spacing: 0.3px; }
  .headline-line { display: block; }
  .source { position: absolute; left: 0; right: 0; top: 876px; text-align: center; font-size: 33px; font-weight: 700; color: var(--ink); }
  .benefits { position: absolute; left: 200px; top: 946px; list-style: none; }
  .benefit { display: flex; align-items: center; height: 37.5px; font-size: 17px; font-weight: 500; color: var(--grey-text); letter-spacing: 0.2px; }
  .benefit svg { width: 22px; height: 22px; margin-right: 25px; }
  .footer-item { position: absolute; top: 1086px; display: flex; align-items: center; color: #fff; font-size: 21px; font-weight: 600; letter-spacing: 0.1px; }
  .footer-item svg { margin-right: 14px; }
  .footer-modes { left: 46px; }
  .footer-scholarship { left: 417px; }
</style>
</head>
<body>
<main class="flyer">
  <svg class="flyer-shapes" viewBox="0 0 803 1139" width="803" height="1139">
    <defs>
      <linearGradient id="officeTone" x1="0" y1="0" x2="1" y2="1">
        <stop offset="0" stop-color="#b9c6d3"/>
        <stop offset="0.5" stop-color="#5b6f84"/>
        <stop offset="1" stop-color="#2a3440"/>
      </linearGradient>
      <linearGradient id="teamTone" x1="0" y1="0" x2="1" y2="1">
        <stop offset="0" stop-color="#aebfd0"/>
        <stop offset="0.55" stop-color="#4f6582"/>
        <stop offset="1" stop-color="#272f3c"/>
      </linearGradient>
      <radialGradient id="globeTone" cx="0.55" cy="1.1" r="0.7">
        <stop offset="0" stop-color="#2b4a78"/>
        <stop offset="1" stop-color="#161a28"/>
      </radialGradient>
    </defs>

    <polygon points="0,0 362,0 378,70 0,70" fill="var(--ink)"/>

    <polygon points="362,0 388,0 474,452 803,452 803,467 455,467" fill="var(--green)"/>
    <g role="img" aria-label="Photo of an IT professional working at dual computer monitors in a modern office">
      <polygon points="388,0 803,0 803,452 474,452" fill="url(#officeTone)"/>
    </g>

    <polygon points="0,365 402,365 414,425 0,425" fill="var(--grey-band)"/>
    <polygon points="410,425 455,425 455,464" fill="var(--ink)"/>

    <polygon points="0,481 315,481 392,862 372,862 303,496 0,496" fill="var(--green)"/>
    <polygon points="315,483 349,517 322,517" fill="var(--grey-band)"/>

    <g role="img" aria-label="Photo of two colleagues reviewing work together at computer monitors">
      <polygon points="0,496 303,496 372,862 0,862" fill="url(#teamTone)"/>
    </g>

    <g role="img" aria-label="Dark backdrop with a glowing view of the earth at night">
      <polygon points="322,517 803,517 803,862 392,862" fill="url(#globeTone)"/>
    </g>

    <rect x="145" y="926" width="512" height="3" fill="var(--green)"/>
    <rect x="356" y="923" width="62" height="9" fill="var(--green)"/>

    <rect x="0" y="1068" width="803" height="71" fill="var(--ink)"/>
  </svg>

  <h1 class="title display">
    <span class="title-line title-desktop">Desktop</span>
    <span class="title-line title-network">&amp; Network</span>
    <span class="title-line title-course">Support Course</span>
  </h1>
  <p class="subtitle sans">MASTER MODERN OPERATING SYSTEMS</p>
  <p class="employment display">90% Employment Rate</p>
  <p class="class-year sans">CLASS OF 2024</p>

  <h2 class="headline display">
    <span class="headline-line">Prepare for 3</span>
    <span class="headline-line">of the top 10</span>
    <span class="headline-line">tech jobs</span>
  </h2>

  <p class="source sans">NATIONAL CAREER OUTLOOK 2025</p>
  <ul class="benefits sans">
    <li class="benefit"><svg viewBox="0 0 22 22" aria-hidden="true"><circle cx="10" cy="11" r="7.5" fill="none" stroke="var(--ink)" stroke-width="2"/><path d="M6.5 10.5l3.2 3.2L19 4" fill="none" stroke="var(--green)" stroke-width="2.4" stroke-linecap="round"/></svg>HANDS-ON DESKTOP &amp; NETWORK TRAINING</li>
    <li class="benefit"><svg viewBox="0 0 22 22" aria-hidden="true"><circle cx="10" cy="11" r="7.5" fill="none" stroke="var(--ink)" stroke-width="2"/><path d="M6.5 10.5l3.2 3.2L19 4" fill="none" stroke="var(--green)" stroke-width="2.4" stroke-linecap="round"/></svg>REAL-WORLD TROUBLESHOOTING SKILLS</li>
    <li class="benefit"><svg viewBox="0 0 22 22" aria-hidden="true"><circle cx="10" cy="11" r="7.5" fill="none" stroke="var(--ink)" stroke-width="2"/><path d="M6.5 10.5l3.2 3.2L19 4" fill="none" stroke="var(--green)" stroke-width="2.4" stroke-linecap="round"/></svg>READY FOR IT JOBS</li>
  </ul>

  <p class="footer-item footer-modes display">
    <svg width="30" height="32" viewBox="0 0 32 34" aria-hidden="true"><circle cx="15" cy="4" r="3.5" fill="var(--green)"/><rect x="11" y="8" width="8" height="9" rx="2" fill="var(--green)"/><rect x="20" y="6" width="4" height="9" fill="var(--green)"/><rect x="2" y="17" width="28" height="4" fill="var(--green)"/><rect x="4" y="21" width="24" height="13" fill="var(--green)"/></svg>
    In-person and remote options
  </p>
  <p class="footer-item footer-scholarship display">
    <svg width="44" height="34" viewBox="0 0 44 34" aria-hidden="true"><polygon points="22,2 43,11 22,20 1,11" fill="var(--green)"/><path d="M10 15v8c0 3 6 5 12 5s12-2 12-5v-8l-12 5z" fill="var(--green)"/><rect x="4" y="12" width="2" height="14" fill="var(--green)"/><rect x="2.5" y="25" width="5" height="7" fill="var(--green)"/></svg>
    Partial scholarships offered
  </p>
</main>
</body>
</html>
```